tinyTally Resource Book - 10 maths tasks to do outside

I need a 22 (11 pages back to back) page A6 sized book produced to standard for submission to professional printer. Needs to be as .pdf file showing guide lines and allowances for colour bleed. I have text already written and submitted as attachment in a Word file with margins set to A6 size. The theme of the materials is "Nature Play" so using lots of pictures from nature (Australia preferably) and showing lots of patterns in nature (rocks, leaves, flower petals etc). Some of the tasks refer to specific activities, such as "shadows" and "floating" so would be great to illustrate appropriately. The big emphasis is on learning outside the classroom, getting kids to engage actively with nature. I would like to see the pages as full colour - so not white background. The book itself will be spiral bound along the top edge so a margin of at least 1cm will be required at the top of each page (or the bottom of even numbered pages). Book will be printed on plastic laminated matte paper for outdoor use. Font size needs to be big enough to read. Fonts sizes, alignments and page numbers are all different at the moment and need to be standardised. One photo is included in a page as a sample if you can use it, otherwise disregard. Logo for Wattlebrook Numeracy Guild is also included to have as part of the acknowledgements at the back of the book.

Target Market(s)

Book is for early childhood and preschool teachers.

Industry/Entity Type

Education

Font styles to use
Sans Serif

Requirements
Must have
• Colour and appeal.
Nice to have
• Use of natural colours instead of bright catchy colours but that is your call.
Should not have
• American spelling

```html
<!DOCTYPE html>
<html lang="en-AU">
<head>
<meta charset="utf-8">
<title>8. Does It Float?</title>
<link href="https://fonts.googleapis.com/css2?family=Jost:wght@400;700;800&display=swap" rel="stylesheet">
<style>
  :root {
    --paper: #ffffff;
    --navy: #2f3a8f;
    --ink: #262a33;
    --diamond: #e1232b;
    --water-top: #f7fbfe;
    --water-mid: #cfe6f5;
    --water-deep: #5fa6d8;
    --trim: #3a3a3a;
  }
  * { margin: 0; padding: 0; box-sizing: border-box; }
  html, body { width: 892px; height: 1200px; overflow: hidden; background: var(--paper); }
  .sheet { position: relative; width: 892px; height: 1200px; }
  .trim-marks { position: absolute; inset: 0; }
  .page-bg {
    position: absolute; left: 52px; top: 0; width: 788px; height: 1146px;
    background: linear-gradient(180deg, var(--water-top) 0%, #eef6fc 28%, var(--water-mid) 52%, #9ccbea 75%, var(--water-deep) 100%);
  }
  .title {
    position: absolute; left: 124px; top: 134px;
    font: 700 54px/1 "Jost", sans-serif; color: var(--navy); letter-spacing: 0.5px;
  }
  .heading {
    position: absolute; left: 125px;
    font: 800 42px/1 "Jost", sans-serif; color: var(--navy);
    text-shadow: 0 0 2px #fff, 0 0 2px #fff, 0 0 3px #fff;
  }
  .points {
    position: absolute; left: 186px; list-style: none;
    font: 400 32px/42px "Jost", sans-serif; color: var(--ink); white-space: nowrap;
  }
  .points li { position: relative; padding-left: 32px; }
  .points li::before {
    content: ""; position: absolute; left: 3px; top: 14px; width: 16px; height: 16px;
    background: var(--diamond); transform: rotate(45deg);
  }
  .photo { position: absolute; }
  .stone { left: 456px; top: 800px; width: 100px; height: 128px; border-radius: 48% 52% 45% 55%; background: linear-gradient(150deg, #a9bf86, #6f8a5d); transform: rotate(-18deg); }
  .ball { left: 600px; top: 798px; width: 120px; height: 120px; border-radius: 50%; background: radial-gradient(circle at 35% 30%, #6fa6e6, #1f4f9c); }
  .apple { left: 454px; top: 944px; width: 92px; height: 104px; border-radius: 46%; background: radial-gradient(circle at 40% 35%, #f04a4a, #b3121b); }
  .leaf { left: 572px; top: 930px; width: 124px; height: 124px; border-radius: 40% 10% 40% 10%; background: linear-gradient(135deg, #f6c23a, #e0641b); transform: rotate(20deg); }
  .page-no {
    position: absolute; left: 696px; top: 1042px; width: 70px; height: 50px;
    display: flex; align-items: center; justify-content: center; padding-top: 6px;
    font: 400 28px/1 "Jost", sans-serif; color: #fff;
  }
  .page-no svg { position: absolute; inset: 0; z-index: 0; }
  .page-no span { position: relative; }
</style>
</head>
<body>
<div class="sheet">
  <div class="page-bg" role="img" aria-label="Photo of rippling clear blue water fading to white at the top"></div>

  <svg class="trim-marks" width="892" height="1200" viewBox="0 0 892 1200" fill="none" stroke="var(--trim)" stroke-width="1">
    <path d="M52 0V48M0 52H48M74 36V74H36"/>
    <path d="M840 0V48M892 52H844M818 36V74H856"/>
    <path d="M52 1200V1152M0 1146H48M74 1164V1126H36"/>
    <path d="M840 1200V1152M892 1146H844M818 1164V1126H856"/>
  </svg>

  <h1 class="title">8. Does It Float?</h1>
  <ul class="points" style="top:201px">
    <li>Half fill a shallow tub with water</li>
    <li>Experiment with objects to find three<br>that float and three that sink</li>
  </ul>

  <h2 class="heading" style="top:356px">Prompting questions</h2>
  <ul class="points" style="top:408px">
    <li>How are the floating objects similar?</li>
    <li>How are the sinking objects similar?</li>
    <li>Can you sink a floating object?</li>
    <li>Can you make a “boat” to support a<br>sinking object?</li>
  </ul>

  <h2 class="heading" style="top:648px">Variations</h2>
  <ul class="points" style="top:699px">
    <li>Make predictions about the floating<br>ability of untested objects then test<br>them</li>
  </ul>

  <h2 class="heading" style="top:854px">Big Ideas</h2>
  <ul class="points" style="top:905px">
    <li>Sinking, floating</li>
    <li>Heavy, light</li>
    <li>Cause, effect</li>
    <li>Prediction</li>
  </ul>

  <div class="photo stone" role="img" aria-label="Photo of a green speckled river stone"></div>
  <div class="photo ball" role="img" aria-label="Photo of a blue inflatable ball"></div>
  <div class="photo apple" role="img" aria-label="Photo of a red apple"></div>
  <div class="photo leaf" role="img" aria-label="Photo of an orange autumn leaf"></div>

  <div class="page-no">
    <svg viewBox="0 0 70 50" width="70" height="50" preserveAspectRatio="none"><polygon points="35,0 70,19 58,50 12,50 0,19" fill="var(--navy)"/></svg>
    <span>17</span>
  </div>
</div>
</body>
</html>
```